Request for Business Card Design

Hi. My name is Marlene, I am looking for a new business card design for my company, Quarrow Signal Instruments, LLC. I really like the design you did for Tarsel Venture and was hoping you could do something similar using our full logo and our mark. I am also open to any raised texture design using our mark. I have attached our full logo, which would need to be somewhere on the card, as well as the mark in both outline and full form, as well as our brand colors / guide. The card does not have to be white, as long as our logo and mark appear. I actually like darker colored business cards more, but am open to all options. If you are interested in working with me, please let me know. We would also take the business card design into letterhead design if you can do that.

```html
<!DOCTYPE html>
<html lang="en">
<head>
<meta charset="utf-8">
<title>Quarrow Signal Instruments – Business Card</title>
<link href="https://fonts.googleapis.com/css2?family=Barlow:wght@400;600&family=Nunito+Sans:wght@400;700&display=swap" rel="stylesheet">
<style>
  :root {
    --backdrop: #e4e4e2;
    --green-dark: #5c9b2c;
    --green-light: #8bc157;
    --ink: #f4f6f1;
    --shadow: rgba(0, 0, 0, 0.28);
  }
  * { margin: 0; padding: 0; box-sizing: border-box; }
  html, body { width: 1200px; height: 1200px; overflow: hidden; }
  body { background: var(--backdrop); position: relative; color: var(--ink); }

  .card {
    position: absolute;
    left: 235px;
    width: 730px;
    height: 418px;
    background: linear-gradient(30deg, var(--green-dark) 0%, #71ae3d 55%, var(--green-light) 100%);
    box-shadow: -10px 14px 26px var(--shadow);
  }
  .card--front { top: 160px; }
  .card--back { top: 632px; }

  .brand { position: absolute; display: flex; align-items: center; font-family: "Barlow", sans-serif; font-weight: 600; color: var(--ink); }
  .brand__dot { border-radius: 50%; border: solid var(--ink); flex: none; }
  .brand__name { line-height: 1; text-transform: uppercase; }
  .brand__line { display: block; }

  .brand--large { left: 100px; top: 150px; gap: 36px; }
  .brand--large .brand__dot { width: 108px; height: 108px; border-width: 16px; }
  .brand--large .brand__main { font-size: 66px; letter-spacing: 6px; }
  .brand--large .brand__sub { font-size: 22px; letter-spacing: 0.5px; margin-top: 8px; }

  .brand--small { left: 416px; top: 300px; gap: 20px; }
  .brand--small .brand__dot { width: 62px; height: 62px; border-width: 9px; }
  .brand--small .brand__main { font-size: 38px; letter-spacing: 3px; }
  .brand--small .brand__sub { font-size: 12.5px; letter-spacing: 0.3px; margin-top: 5px; }

  .person { position: absolute; left: 45px; top: 56px; font-family: "Nunito Sans", sans-serif; }
  .person__name { font-size: 27px; font-weight: 700; line-height: 1.1; }
  .person__title { font-size: 18px; font-weight: 400; margin-top: 8px; }

  .address { position: absolute; left: 44px; top: 180px; font-family: "Barlow", sans-serif; font-size: 19.5px; line-height: 28px; letter-spacing: 0.6px; font-style: normal; }

  .contacts { position: absolute; left: 44px; top: 254px; list-style: none; font-family: "Barlow", sans-serif; font-size: 19.5px; letter-spacing: 0.6px; }
  .contacts li { display: flex; align-items: center; height: 26px; }
  .contacts svg { width: 16px; height: 16px; margin-right: 10px; fill: var(--ink); flex: none; }
</style>
</head>
<body>

<section class="card card--front">
  <div class="brand brand--large">
    <span class="brand__dot"></span>
    <span class="brand__name">
      <span class="brand__line brand__main">Quarrow</span>
      <span class="brand__line brand__sub">Signal Instruments</span>
    </span>
  </div>
</section>

<section class="card card--back">
  <div class="person">
    <h1 class="person__name">Marlene</h1>
    <p class="person__title">Founder &amp; Director</p>
  </div>

  <address class="address">
    1180 Harbor Works Avenue.<br>
    Fenwick, CO 80999
  </address>

  <ul class="contacts">
    <li>
      <svg viewBox="0 0 16 16" aria-hidden="true"><path d="M3.5 1.5l2.3 3-1.3 1.6c.8 1.8 2.2 3.2 4 4l1.6-1.3 3 2.3-1.4 2.4C7 13.5 2.5 9 1.1 2.9z"/></svg>
      +001 555 210 4408
    </li>
    <li>
      <svg viewBox="0 0 16 16" aria-hidden="true"><path d="M4 1h8v4H4zM1 6h14v6h-3v3H4v-3H1zm4 4v4h6v-4z"/></svg>
      +001 555 210 4419
    </li>
    <li>
      <svg viewBox="0 0 16 16" aria-hidden="true"><path d="M1 3h14v1.2L8 9 1 4.2zM1 5.8l7 4.8 7-4.8V13H1z"/></svg>
      info@quarrowsignal.com
    </li>
    <li>
      <svg viewBox="0 0 16 16" aria-hidden="true"><path d="M8 1a7 7 0 100 14A7 7 0 008 1zm-1 2.2V7H3.1A5 5 0 017 3.2zm2 0A5 5 0 0112.9 7H9zM3.1 9H7v3.8A5 5 0 013.1 9zM9 9h3.9A5 5 0 019 12.8z"/></svg>
      www.quarrowsignal.com
    </li>
  </ul>

  <div class="brand brand--small">
    <span class="brand__dot"></span>
    <span class="brand__name">
      <span class="brand__line brand__main">Quarrow</span>
      <span class="brand__line brand__sub">Signal Instruments</span>
    </span>
  </div>
</section>

</body>
</html>
```